Verpackungen für Klangschalenuhren
Zielgruppe
Unter der Marke 'Velumor' werden manufakturartig Klangschalenuhren in geringen Stückzahlen hergestellt. Produktionsort ist Deutschland, bis auf die Klangschalen.
Bei Klangschalenuhren wird mechanisch eine Klangschale angeschlagen.
Vorteile / Einsatz: Sanftes Aufwachen mit einer Klangschale / Ambiente: Hauch von Asien im Wohnbereich / Meditation & Wellness / Sitzungen, Behandlungen und Meetings
Zielgruppe:
„LOHAS“: kaufkräftig, bewusstes Leben, gesundheitsorientiert, natürliche/nachhaltige Produkte, Fairtrade/ethisches Handeln, authentisch. Selbständige (z.B. Therapeuten). Wellness.
Aufgabenstellung
Die Produktverpackung steht nicht im Verkaufsregal und muss daher kaum informative Elemente über das Produkt enthalten. Der Kunde sieht Verpackung beim Auspacken aus Versandkarton oder im Onlineshop.
WERTIG, NATÜRLICH, SCHLICHT. Kunde soll bei Empfang und Auspacken seines Produkts Freude empfinden.
Es gibt nur eine Verpackung für viele Modelle / Produktvarianten -> Produktfotos nicht geeignet.
Designelemente (Minimum):
Logo mit Claim „Die Ruhe im Takt“. Mindestens auf Frontseite und Klappdeckel.
Ergänzen um ein stilisiertes Bild mit einer (angeschnittenen) Klangschale mit Klöppel
Handwerk aus Deutschland (mit oder ohne Symbol)
Adressdaten:
Velumor
Lindenhofstraße 14
64682 Birkenau-Ostheim
Deutschland
www.velumor.de
Feld für Artikelaufkleber: 5 x 3 cm (bxh)
Zu bedruckender Karton:
Steckbodenschachtel
Größe 245 x 245 x 205 mm
aus Mikrowellpappe E-Welle innen braun
kaschiert mit GD2-Karton 230 g/qm
4/0-farbig bedruckt u. Dispersionsglanzlack

```html
<!DOCTYPE html>
<html lang="de">
<head>
<meta charset="utf-8">
<title>Velumor – Verpackung Klangschalenuhr</title>
<link rel="stylesheet" href="https://fonts.googleapis.com/css2?family=Didact+Gothic&family=Raleway:wght@300&display=swap">
<style>
  :root {
    --page: #ffffff;
    --cream: #f7ecd9;
    --sand: #efd9b6;
    --ink: #333333;
    --cut: #2aa84a;
    --fold: #3a3a3a;
    --gold-soft: #e6d2b0;
    --label: #faf4ea;
  }
  html, body {
    margin: 0;
    width: 1200px;
    height: 903px;
    overflow: hidden;
    background: var(--page);
  }
  .sheet { display: block; width: 1200px; height: 903px; }
  .brand { font-family: "Didact Gothic", sans-serif; fill: var(--ink); }
  .claim, .tagline, .product { font-family: "Raleway", sans-serif; font-weight: 300; fill: var(--ink); }
  .address, .poem { font-family: "Didact Gothic", sans-serif; fill: var(--ink); }
  .web { font-family: "Didact Gothic", sans-serif; fill: var(--gold-soft); }
  .cut { fill: none; stroke: var(--cut); stroke-width: 1.6; }
  .fold { fill: none; stroke: var(--fold); stroke-width: 1.4; }
  .sticker-field { fill: var(--label); }
</style>
</head>
<body>
<svg class="sheet" viewBox="0 0 2000 1505" xmlns="http://www.w3.org/2000/svg">
  <defs>
    <linearGradient id="panel-shade" x1="0" x2="1" y1="0" y2="0">
      <stop offset="0" stop-color="#f7ebd8"/>
      <stop offset="0.55" stop-color="#f6e9d4"/>
      <stop offset="1" stop-color="#efdab8"/>
    </linearGradient>
    <linearGradient id="panel-shade-rev" x1="1" x2="0" y1="0" y2="0">
      <stop offset="0" stop-color="#efd9b6"/>
      <stop offset="0.5" stop-color="#f6e9d4"/>
      <stop offset="1" stop-color="#f7ebd8"/>
    </linearGradient>
    <linearGradient id="edge-shade" x1="0" x2="1" y1="0" y2="0">
      <stop offset="0" stop-color="#efd9b6"/>
      <stop offset="1" stop-color="#f7ebd8"/>
    </linearGradient>
    <linearGradient id="bowl-tones" x1="0" x2="1" y1="0" y2="1">
      <stop offset="0" stop-color="#f5e4c4"/>
      <stop offset="1" stop-color="#ecd19c"/>
    </linearGradient>
  </defs>

  <!-- standalone wordmark -->
  <text class="brand" x="130" y="185" font-size="118">Velumor</text>

  <!-- print area -->
  <g class="print-area">
    <rect x="109" y="318" width="519" height="380" fill="var(--cream)"/>
    <rect x="109" y="690" width="1831" height="785" fill="var(--cream)"/>
    <rect x="109" y="318" width="55" height="872" fill="url(#edge-shade)"/>
    <rect x="597" y="690" width="435" height="500" fill="url(#panel-shade)"/>
    <rect x="1032" y="690" width="435" height="500" fill="url(#panel-shade-rev)"/>
    <rect x="1467" y="690" width="473" height="500" fill="url(#panel-shade)"/>
  </g>

  <!-- die line: cuts -->
  <g class="dieline">
    <path class="cut" d="M163 368 V360 Q163 328 200 328 H560 Q597 328 597 360 V368"/>
    <path class="cut" d="M163 368 V806 M597 368 V722"/>
    <path class="cut" d="M163 810 L128 820 V1160 L163 1170"/>
    <path class="cut" d="M597 806 V722 H1007 L1025 790 L1032 792 V806"/>
    <path class="cut" d="M1032 806 H1467"/>
    <path class="cut" d="M1467 806 V792 L1475 788 L1493 722 H1900 V806"/>
    <path class="cut" d="M163 1170 L270 1385 V1402 Q270 1417 285 1417 H475 Q489 1417 489 1402 V1385 L597 1170"/>
    <path class="cut" d="M597 1170 V1377 H813 V1277 L1032 1170"/>
    <path class="cut" d="M1032 1170 V1417 H1140 V1383 H1360 V1417 H1467 V1170"/>
    <path class="cut" d="M1467 1170 L1687 1277 V1377 H1900 V1170"/>
    <path class="cut" d="M1232 808 A18 18 0 0 0 1268 808"/>
  </g>

  <!-- die line: folds -->
  <g class="folds">
    <path class="fold" d="M185 370 H328 M330 368 H432 M434 370 H577"/>
    <path class="fold" d="M163 806 H1032 M1467 806 H1900"/>
    <path class="fold" d="M163 1170 H1900"/>
    <path class="fold" d="M163 806 V1170 M597 806 V1170 M1032 806 V1170 M1467 806 V1170 M1900 806 V1170"/>
    <path class="fold" d="M1197 808 V785 Q1197 773 1210 773 H1290 Q1303 773 1303 785 V808 M1197 808 V842 H1303 V808" stroke-width="1.2"/>
  </g>

  <!-- lid -->
  <g class="panel-lid">
    <text class="brand" x="380" y="605" font-size="62" text-anchor="middle">Velumor</text>
    <text class="claim" x="380" y="650" font-size="25" text-anchor="middle">Die Ruhe im Takt</text>
  </g>

  <!-- front -->
  <g class="panel-front">
    <text class="brand" x="380" y="965" font-size="62" text-anchor="middle">Velumor</text>
    <rect x="180" y="998" width="200" height="162" fill="url(#bowl-tones)" opacity="0.55"
          role="img" aria-label="Stilisierte Klangschale mit Klöppel, goldene Linienzeichnung"/>
    <text class="product" x="383" y="1148" font-size="19">KLANGSCHALENUHR</text>
  </g>

  <!-- side -->
  <g class="panel-side">
    <text class="tagline" x="810" y="1038" font-size="31" text-anchor="middle">Die perfekte Verbindung</text>
    <text class="tagline" x="812" y="1073" font-size="31" text-anchor="middle">von Klang und Zeit.</text>
  </g>

  <!-- back -->
  <g class="panel-back">
    <text class="brand" x="1073" y="985" font-size="34">Velumor</text>
    <text class="product" x="1075" y="1038" font-size="29">KLANGSCHALENUHR</text>
    <g class="address" font-size="11.5">
      <text x="1075" y="1074">Velumor</text>
      <text x="1075" y="1091">Lindenhofstraße 14</text>
      <text x="1075" y="1104">64682 Birkenau-Ostheim</text>
      <text x="1075" y="1118">Deutschland</text>
    </g>
    <text class="web" x="1075" y="1145" font-size="25">www.velumor.de</text>
    <rect class="sticker-field" x="1352" y="1096" width="90" height="54"/>
  </g>

  <!-- poem side -->
  <g class="poem" font-size="9.8" text-anchor="middle">
    <text x="1680" y="1015">Wir glauben seit Ewigkeiten, dass wir die Zeit nicht anhalten können.</text>
    <text x="1680" y="1034">Dass sie läuft in atemloser Schnelle.</text>
    <text x="1680" y="1052">Bis uns ein Klang berührt und ergreift.</text>
    <text x="1680" y="1071">Es ist der Ton einer Velumor, der uns inne halten lässt.</text>
    <text x="1680" y="1090">Er trägt uns fort mit leise wachsender Kraft.</text>
    <text x="1680" y="1109">Ins grenzenlose Ich und zurück.</text>
    <text x="1680" y="1128">Wir hören den Klang der Zeit und lächeln unendlich beglückt.</text>
    <text x="1680" y="1146">Denn wir sind ewig. Für diesen Moment.</text>
  </g>
</svg>
</body>
</html>
```